New Business Card Design Project

Need a design that will create an impact / strong impression towards our clients for our business. We are in the lighting business and we do lighting retrofits for large commercial to industrial clientele.

Target Market(s)

Lighting Industry

Industry/Entity Type

Business

Font styles to use
Other font styles liked:
• we would like to use the font on our logo, not sure what it is though..

Requirements
Must have
• Our logo.
Nice to have
• We are open to suggestions that have to do with lighting.

```html
<!DOCTYPE html>
<html lang="en">
<head>
<meta charset="utf-8">
<title>Lumen Retrofit Partners — Business Card</title>
<link href="https://fonts.googleapis.com/css2?family=Lato:wght@400;700&display=swap" rel="stylesheet">
<style>
  :root {
    --bg: #1e1e1e;
    --green-deep: #0f3d1c;
    --green-mid: #1f5e2c;
    --green-brand: #1d8a3c;
    --green-light: #6cc24a;
    --green-dark-block: #1f3a1c;
    --ink: #5c5c5c;
    --white: #ffffff;
  }
  * { margin: 0; padding: 0; box-sizing: border-box; }
  html, body { width: 1200px; height: 897px; overflow: hidden; }
  body { background: var(--bg); font-family: "Lato", sans-serif; position: relative; }

  .card { position: absolute; }

  .card-front {
    left: 308px; top: 108px; width: 576px; height: 329px;
    background: radial-gradient(ellipse at 75% 10%, var(--green-mid) 0%, var(--green-deep) 75%);
  }
  .front-brand {
    position: absolute; left: 0; right: 0; top: 130px;
    display: flex; justify-content: center; align-items: center; gap: 12px;
    color: var(--white); font-weight: 700; font-size: 30px; letter-spacing: 2px;
    text-transform: uppercase;
  }
  .brand-square { width: 18px; height: 18px; background: var(--green-light); }
  .front-web {
    position: absolute; left: 0; right: 0; top: 292px; text-align: center;
    color: var(--white); font-size: 13px; letter-spacing: 1.5px;
  }
  .front-web .accent { color: var(--green-light); }

  .card-back {
    left: 301px; top: 471px; width: 583px; height: 330px;
    background: var(--white); overflow: hidden;
  }
  .back-brand {
    position: absolute; left: 27px; top: 48px;
    display: flex; align-items: center; gap: 10px;
    color: var(--green-brand); font-weight: 700; font-size: 24px; letter-spacing: 1.5px;
    text-transform: uppercase;
  }
  .back-brand .brand-square { width: 14px; height: 14px; }
  .person { position: absolute; right: 28px; top: 166px; text-align: right; }
  .person-name { color: var(--green-brand); font-size: 19px; letter-spacing: 0.5px; line-height: 1.1; }
  .person-role { color: var(--ink); font-size: 15px; line-height: 1.3; }
  .divider { position: absolute; left: 27px; width: 528px; top: 216px; height: 2px; background: var(--green-light); }

  .contacts { position: absolute; left: 27px; top: 228px; list-style: none; }
  .contacts li { display: flex; align-items: center; gap: 12px; color: var(--ink); font-size: 13.5px; height: 18.5px; }
  .contacts svg { width: 11px; height: 11px; fill: var(--green-brand); }

  .address { position: absolute; right: 28px; top: 228px; text-align: right; color: var(--ink); font-size: 13.5px; line-height: 18.5px; }

  .base-band { position: absolute; left: 0; bottom: 0; width: 583px; height: 9px; background: var(--green-light); }
  .base-block { position: absolute; right: 0; bottom: 0; width: 160px; height: 36px; background: var(--green-dark-block); }
</style>
</head>
<body>
  <section class="card card-front">
    <div class="front-brand"><span class="brand-square"></span>Lumen Retrofit Partners</div>
    <p class="front-web">www.<span class="accent">lumenretrofit</span>.com</p>
  </section>

  <section class="card card-back">
    <div class="back-brand"><span class="brand-square"></span>Lumen Retrofit Partners</div>

    <div class="person">
      <p class="person-name">DANIEL CARTER</p>
      <p class="person-role">Founder</p>
    </div>
    <div class="divider"></div>

    <ul class="contacts">
      <li><svg viewBox="0 0 24 24"><path d="M6.6 10.8a15 15 0 0 0 6.6 6.6l2.2-2.2c.3-.3.7-.4 1-.2 1.1.4 2.3.6 3.6.6.6 0 1 .4 1 1V20c0 .6-.4 1-1 1A17 17 0 0 1 3 4c0-.6.4-1 1-1h3.5c.6 0 1 .4 1 1 0 1.3.2 2.5.6 3.6.1.3 0 .7-.2 1z"/></svg>0400 555 019</li>
      <li><svg viewBox="0 0 24 24"><path d="M2 5h20v14H2z M2 5l10 8 10-8" /></svg>info@lumenretrofit.com</li>
      <li><svg viewBox="0 0 24 24"><circle cx="12" cy="12" r="10"/></svg>www.lumenretrofit.com</li>
    </ul>

    <p class="address">4820 Harbor Lane,<br>Suite Mesa 85201</p>

    <div class="base-band"></div>
    <div class="base-block"></div>
  </section>
</body>
</html>
```